Home Remodeling company needs a business card design

we need a business card design for home remodeling company in hamilton county, indiana USA. we offers a wide range of construction services including whole house renovations, Design and Build Basements and Kitchen and Bathroom Remodeling . we would like to see designs for both site of business card that use the same color of the company logo and also including all information below :
1- Karim Feltous CEO / General Contractor
2- all company contacts Telephone numbers ( 1-888-DULOM-47 ) ( 317-555-0193) email address ( info@dulomhome.com) website ( www.dulomhome.com ) and social media logos (Facebook- twitter- google plus )
3- company logo
4- licensed . insured . bonded

```html
<!DOCTYPE html>
<html lang="en">
<head>
<meta charset="utf-8">
<title>Dulom Home Remodeling — Business Card</title>
<link rel="stylesheet" href="https://fonts.googleapis.com/css2?family=Open+Sans:wght@400;600;700&display=swap">
<style>
  :root {
    --stage: #3a3230;
    --card: #141414;
    --card-glow: #2a2a2a;
    --red: #d0333f;
    --white: #f4f4f4;
    --name-grey: #8a8a8a;
  }
  * { box-sizing: border-box; margin: 0; padding: 0; }
  html, body {
    width: 1200px; height: 844px; overflow: hidden;
    background: var(--stage);
  }
  .canvas {
    position: relative; width: 1200px; height: 844px;
    font-family: "Open Sans", Arial, sans-serif;
  }
  .card {
    position: absolute; top: 273px;
    width: 520px; height: 298px;
    background: var(--card);
    overflow: hidden;
    box-shadow: 0 10px 30px rgba(0,0,0,0.45);
  }

  /* Contact side */
  .card--contact { left: 50px; }
  .card--contact .band {
    position: absolute; left: 0; right: 0; height: 16px; background: var(--red);
  }
  .band--top { top: 0; }
  .band--bottom { bottom: 0; }
  .contact {
    position: absolute; top: 34px; left: 0; right: 0;
    text-align: center; color: var(--white);
  }
  .contact__name { color: var(--red); font-weight: 700; font-size: 15px; line-height: 18px; }
  .contact__title { font-size: 12.5px; line-height: 16px; }
  .contact__lines { margin-top: 22px; font-size: 12.5px; line-height: 17px; }
  .social { display: flex; justify-content: center; gap: 10px; margin-top: 20px; }
  .social__dot {
    width: 24px; height: 24px; border-radius: 50%;
    background: var(--white);
  }
  .credentials {
    margin-top: 20px; font-weight: 700; font-size: 16px; letter-spacing: 0.2px;
  }

  /* Name side */
  .card--brand {
    left: 630px;
    background: radial-gradient(ellipse 60% 55% at 50% 42%, var(--card-glow), var(--card) 75%);
  }
  .tab {
    position: absolute; width: 24px; height: 34px; background: var(--red);
    border-right: 4px solid var(--white);
  }
  .tab--left { left: 0; top: 176px; }
  .tab--right { right: 0; top: 40px; border-right: none; border-left: 4px solid var(--white); }
  .brand {
    position: absolute; left: 0; right: 0; top: 132px;
    display: flex; align-items: center; justify-content: center; gap: 10px;
  }
  .brand__mark { width: 10px; height: 10px; background: var(--name-grey); }
  .brand__name {
    font-weight: 600; font-size: 24px; line-height: 30px;
    color: var(--name-grey);
  }
</style>
</head>
<body>
<main class="canvas">

  <section class="card card--contact" aria-label="Contact side of the card">
    <div class="band band--top"></div>
    <div class="contact">
      <p class="contact__name">Karim Feltous</p>
      <p class="contact__title">CEO / General Contractor</p>
      <div class="contact__lines">
        <p>1-888-DULOM-47</p>
        <p>317-555-0193</p>
        <p>info@dulomhome.com</p>
        <p>www.dulomhome.com</p>
      </div>
      <div class="social" aria-label="Social media links">
        <span class="social__dot"></span>
        <span class="social__dot"></span>
        <span class="social__dot"></span>
      </div>
      <p class="credentials">Licensed . Insured . Bonded</p>
    </div>
    <div class="band band--bottom"></div>
  </section>

  <section class="card card--brand" aria-label="Company name side of the card">
    <div class="tab tab--right"></div>
    <div class="tab tab--left"></div>
    <div class="brand">
      <span class="brand__mark"></span>
      <p class="brand__name">Dulom Home Remodeling</p>
    </div>
  </section>

</main>
</body>
</html>
```